Award-winnning Estate Agent needs a premium version of their 'For Sale' board design

We need a premium option for our 'For Sale' board design. We have a standard board that is attached to this brief, but were are looking to have a premium design version that we will use when selling exclusive properties. Our company name is Harbourline Vale Estates and the name for this is exclusive selection is: 'The Harbourline Collection'. The design needs to work with our current brand, but have a distinctive PREMIUM feel to it. I have uploaded the barnd guidelines and also some of the exisisting logo variations. We do NOT need a new logo but feel free to play around with colours, fonts, sizes etc. for the sign.

Target Market(s)

Property buyers & house hunters

Industry/Entity Type

Real Estate - Residential Property

Font styles to use
Sans Serif

Requirements
Must have
• A premium fee, must be square design, must be easy to read when driving past the sign
Nice to have
• I'm open ot ideas

```html
<!DOCTYPE html>
<html lang="en">
<head>
<meta charset="utf-8">
<title>Harbourline Vale Estates – For Sale Board</title>
<link rel="stylesheet" href="https://fonts.googleapis.com/css2?family=Archivo+Black&family=Roboto:wght@500;700&display=swap">
<style>
  :root {
    --navy: #283891;
    --sky: #29a8e0;
    --white: #ffffff;
    --page: #ffffff;
    --display: "Archivo Black", "Arial Black", sans-serif;
    --text: "Roboto", "Helvetica Neue", Arial, sans-serif;
  }
  * { margin: 0; padding: 0; box-sizing: border-box; }
  html, body {
    width: 1200px;
    height: 621px;
    overflow: hidden;
    background: var(--page);
  }
  .canvas {
    position: relative;
    width: 1200px;
    height: 621px;
  }
  .sale-board {
    position: absolute;
    left: 320px;
    top: 30px;
    width: 560px;
    height: 560px;
    background: var(--white);
    box-shadow: 0 2px 6px rgba(0, 0, 0, 0.18);
    color: var(--white);
  }
  .headline-band {
    position: absolute;
    left: 0; top: 0;
    width: 100%;
    height: 125px;
    background: var(--navy);
    display: flex;
    align-items: center;
    justify-content: center;
  }
  .headline {
    font-family: var(--display);
    font-size: 84px;
    line-height: 1;
    letter-spacing: 1px;
    padding-top: 6px;
  }
  .brand-panel {
    position: absolute;
    left: 24px;
    top: 125px;
    width: 512px;
    height: 412px;
    background: var(--sky);
  }
  .brand-dot {
    position: absolute;
    left: 50%;
    top: 52px;
    width: 64px;
    height: 64px;
    margin-left: -32px;
    border-radius: 50%;
    background: var(--white);
  }
  .brand-name {
    position: absolute;
    left: 0; top: 164px;
    width: 100%;
    text-align: center;
    font-family: var(--text);
    font-weight: 500;
    font-size: 34px;
    line-height: 1;
  }
  .collection-tab {
    position: absolute;
    left: 94px;
    top: 349px;
    width: 372px;
    height: 35px;
    background: var(--navy);
    display: flex;
    align-items: center;
    justify-content: center;
    font-family: var(--text);
    font-weight: 700;
    font-size: 27px;
    line-height: 1;
    padding-top: 4px;
    white-space: nowrap;
  }
  .phone-band {
    position: absolute;
    left: 0; top: 383px;
    width: 100%;
    height: 79px;
    background: var(--navy);
    display: flex;
    align-items: center;
    justify-content: center;
  }
  .phone {
    font-family: var(--display);
    font-size: 62px;
    line-height: 1;
    letter-spacing: 0.5px;
    padding-top: 4px;
  }
  .web-address {
    position: absolute;
    left: 0; top: 490px;
    width: 100%;
    text-align: center;
    font-family: var(--text);
    font-weight: 700;
    font-size: 29px;
    line-height: 1;
  }
</style>
</head>
<body>
  <main class="canvas">
    <section class="sale-board" aria-label="For Sale board">
      <div class="headline-band">
        <h1 class="headline">FOR SALE</h1>
      </div>
      <div class="brand-panel">
        <span class="brand-dot" aria-hidden="true"></span>
        <p class="brand-name">Harbourline Vale Estates</p>
      </div>
      <div class="collection-tab">The Harbourline Collection</div>
      <div class="phone-band">
        <p class="phone">01632 960418</p>
      </div>
      <p class="web-address">www.harbourlinevaleestates.co.uk</p>
    </section>
  </main>
</body>
</html>
```